Hula-Hoop dance entertainment sales and instruction by spin-wavelet needs a business card

I need a 2 sided business card that is square (although this is not an absolute )for my self employed business as an independent artist. my business name is "Spin-Wavelet" I teach how to hula-hoop classes, make and sell hula-hoops, provided entertainment at kids birthday parties, community events, corporate events and perform at artistic dance shows.
I would like to see spirals or curved lines in the card, and I would like the card to be seen as fun, spunky, flair and eye catching.

the card could double as a tag to go on the hoops i sell,

Target Market(s)

women age 20 - 50

Industry/Entity Type

Entertainment

Requirements
Must have
• Dorine Vantash
www.spinwavelet.example
555.014.7263
Nice to have
• I would like my image to be on one side of the card. so people can recognize me!

```html
<!DOCTYPE html>
<html lang="en">
<head>
<meta charset="utf-8">
<title>Dorine Vantash – Hoop Dance Card</title>
<link rel="stylesheet" href="https://fonts.googleapis.com/css2?family=Emilys+Candy&family=Open+Sans:wght@400;700&display=swap">
<style>
  :root {
    --card-bg: #9fa3d3;
    --ink: #000000;
    --frame: #000000;
  }
  html, body {
    margin: 0;
    padding: 0;
    width: 1200px;
    height: 1200px;
    overflow: hidden;
    background: var(--card-bg);
  }
  .card {
    position: relative;
    width: 1200px;
    height: 1200px;
    box-sizing: border-box;
    border: 10px solid var(--frame);
    background: var(--card-bg);
    color: var(--ink);
    font-family: "Open Sans", sans-serif;
  }
  .card__name {
    position: absolute;
    left: 0;
    right: 0;
    top: 50px;
    margin: 0;
    text-align: center;
    font-family: "Emilys Candy", cursive;
    font-weight: 400;
    font-size: 138px;
    line-height: 170px;
    letter-spacing: 2px;
  }
  .card__rule {
    position: absolute;
    left: 145px;
    width: 888px;
    height: 4px;
    background: var(--ink);
  }
  .card__rule--top { top: 254px; }
  .card__rule--bottom { top: 919px; }
  .card__services {
    position: absolute;
    left: 0;
    right: 0;
    top: 287px;
    margin: 0;
    padding: 0;
    list-style: none;
    text-align: center;
    font-size: 47px;
    line-height: 66px;
  }
  .card__contact {
    position: absolute;
    left: 0;
    right: 0;
    top: 955px;
    margin: 0;
    text-align: center;
    font-weight: 700;
    font-size: 58px;
    line-height: 80px;
  }
  .card__contact span { display: block; }
</style>
</head>
<body>
  <main class="card">
    <h1 class="card__name">Dorine Vantash</h1>
    <div class="card__rule card__rule--top"></div>
    <ul class="card__services">
      <li>Hoop Classes</li>
      <li>Hoop Jams</li>
      <li>Private Lessons</li>
      <li>Custom hula-hoops for adults and kids</li>
      <li>Performances</li>
      <li>Hoop Making Workshops</li>
      <li>Birthday Parties</li>
      <li>Corporate Event Entertainment</li>
      <li>and more!</li>
    </ul>
    <div class="card__rule card__rule--bottom"></div>
    <p class="card__contact">
      <span class="card__web">www.spinwavelet.example</span>
      <span class="card__phone">555.014.7263</span>
    </p>
  </main>
</body>
</html>
```